Tavel Website

Need a 4 page Drupal website - Home, About Us, Portfolio, Contact for a private equity/venture capital firm and new logo - company name is Tavel Corporation. The design should communicate - stock markets, hedge funds, deal-making, investments. The Portfolio section is to showcase the small companies we invest in. Hoping for something fresh, dynamic, even fun - no cliche financial images of New York. Not technical - but know how use Drupal content management to make text edits, blocks, articles, etc. We don't use any social media - so no chirply, Pagebook or WorkNode links. We need space for a post heron email sign-up form. Need website uploaded to my Corvane web hosting account. First time user of Sketch Plaza - have 3 other company websites that need refreshing.

```html
<!DOCTYPE html>
<html lang="en">
<head>
<meta charset="utf-8">
<title>Tavel Corporation</title>
<link rel="stylesheet" href="https://fonts.googleapis.com/css2?family=Alegreya+Sans:wght@300;400;500;700;800&display=swap">
<style>
:root{
  --blue:#1e88e5;
  --blue-dark:#1976d2;
  --gold:#f2c14e;
  --ink:#333333;
  --muted:#8a8a8a;
  --rule:#cfcfcf;
  --footer:#262626;
  --white:#ffffff;
  --black:#0b0b0b;
}
*{margin:0;padding:0;box-sizing:border-box}
html,body{width:852px;height:1200px;overflow:hidden;background:var(--white)}
body{position:relative;font-family:"Alegreya Sans",sans-serif;color:var(--ink)}
.abs{position:absolute}

/* header */
.site-header{left:0;top:0;width:852px;height:60px;background:var(--blue)}
.brand{left:125px;top:14px;font-size:22px;font-weight:500;color:var(--white);letter-spacing:.2px}
.main-nav a{position:absolute;top:27px;font-size:9.5px;color:var(--white);text-decoration:none}
.main-nav .active::after{content:"";position:absolute;left:0;right:0;top:15px;height:2px;background:var(--white)}

/* hero */
.hero{left:0;top:60px;width:852px;height:277px;
  background:
    radial-gradient(ellipse at 75% 40%,rgba(60,190,90,.45),transparent 55%),
    radial-gradient(ellipse at 55% 70%,rgba(200,40,40,.35),transparent 50%),
    linear-gradient(100deg,#1c1c22 0%,#2a2f35 45%,#3b4a3e 70%,#20252a 100%)}
.hero-kicker{left:124px;top:116px;font-size:21px;font-weight:300;color:var(--white)}
.hero-title{left:123px;top:147px;font-size:34px;font-weight:800;color:var(--white);letter-spacing:-.3px}
.hero-text{left:126px;top:199px;width:280px;font-size:8px;line-height:14.4px;color:var(--white)}
.btn-read{left:126px;top:245px;width:76px;height:31px;background:var(--blue);color:var(--white);
  font-size:10px;display:flex;align-items:center;justify-content:center;border-radius:2px}
.slider-dots span{position:absolute;top:314px;width:5px;height:5px;border-radius:50%;background:var(--blue)}
.slider-dots .on{background:var(--white)}

/* newsletter */
.newsletter{left:0;top:337px;width:852px;height:90px;background:var(--blue)}
.nl-title{left:131px;top:22px;font-size:13.5px;font-weight:400;color:var(--white);letter-spacing:.2px}
.nl-title em{font-style:normal;color:var(--gold)}
.nl-sub{left:131px;top:46px;width:210px;font-size:6.6px;line-height:10.5px;color:#d8e9fb}
.field{top:27px;width:130px;height:32px;background:var(--white);font-size:6.6px;color:#9a9a9a;padding:13px 11px}
.btn-submit{left:643px;top:27px;width:63px;height:32px;background:var(--black);color:var(--white);
  font-size:8.5px;font-weight:700;display:flex;align-items:center;justify-content:center}

/* welcome */
.welcome-title{left:0;top:462px;width:852px;text-align:center;font-size:14px;font-weight:700;color:var(--ink)}
.welcome-title span{color:var(--blue);margin-left:5px}
.welcome-photo{left:128px;top:512px;width:271px;height:180px;
  background:linear-gradient(180deg,#bdbdbd 0%,#8e8e8e 45%,#3d4450 75%,#2a5fa8 100%)}
.welcome-copy{left:420px;top:510px;width:300px;font-family:Arial,Helvetica,sans-serif;font-size:8px;line-height:12.1px;color:var(--muted)}
.welcome-copy p{margin-bottom:12.2px}

/* section heads */
.section-head{font-size:14px;font-weight:700;color:var(--ink)}
.section-head span{color:var(--blue)}
.rule{height:1px;background:var(--rule)}

/* tips */
.tip-photo{top:803px;width:140px;height:78px}
.tip-title{top:898px;font-size:8.8px;font-weight:700;color:var(--ink)}
.tip-text{top:917px;width:140px;font-family:Arial,Helvetica,sans-serif;font-size:7.5px;line-height:9.6px;color:var(--muted)}

/* portfolio */
.carousel-arrow{top:1002px}
.client{top:1066px;height:22px;display:flex;align-items:center;gap:4px;font-size:11px;font-weight:700;white-space:nowrap}
.client i{display:inline-block;width:11px;height:11px;border-radius:50%}

/* footer */
.site-footer{left:0;top:1129px;width:852px;height:71px;background:var(--footer)}
.footer-nav a{position:absolute;top:20px;font-size:9.5px;color:var(--white);text-decoration:none}
.copyright{left:0;top:42px;width:848px;text-align:center;font-size:7px;color:#bdbdbd}
</style>
</head>
<body>

<header class="site-header abs">
  <div class="brand abs">Tavel Corporation</div>
  <nav class="main-nav">
    <a class="active" style="left:514px">Home</a>
    <a style="left:567px">About Us</a>
    <a style="left:631px">Portfolio</a>
    <a style="left:694px">Contact</a>
  </nav>
</header>

<section class="hero abs" role="img" aria-label="Close-up photo of a stock market ticker board with a pen pointing at glowing green and red price charts"></section>
<div class="hero-kicker abs">How to invest in stocks using best</div>
<div class="hero-title abs">Stock market</div>
<p class="hero-text abs">So you have heard that the market is making new highs everyday (or at least seems that way), and you would like to participate in the rally.</p>
<div class="btn-read abs">Read more</div>
<div class="slider-dots"><span class="on" style="left:411px"></span><span style="left:423px"></span><span style="left:435px"></span></div>

<section class="newsletter abs">
  <h2 class="nl-title abs">SIGN UP FOR <em>NEWSLETTER</em></h2>
  <p class="nl-sub abs">Includes latest reviews, offers and &nbsp;participate for start investing in the &nbsp;Stock market</p>
  <div class="field abs" style="left:364px">Name</div>
  <div class="field abs" style="left:504px">Email</div>
  <div class="btn-submit abs">SUBMIT</div>
</section>

<h2 class="welcome-title abs">WELCOME TO <span>TAVEL CORPORATION</span></h2>
<div class="welcome-photo abs" role="img" aria-label="Photo of a businessman in a suit touching a screen of rising line and bar charts"></div>
<div class="welcome-copy abs">
  <p>So you have heard that the market is making new highs everyday (or at least seems that way), and you would like to participate in the rally. You wonder, how do I do that? Well, this page is intended to provide some basic information on how to start investing in the market.</p>
  <p>First thing first, keep in mind that the market does not offer any guarantees. The fact that an analyst recommends a stock does not mean that the stock is going to go up. Keep in mind that INFORMATION is your best friend in the market. Study the company before you invest.</p>
  <p>Another important tool of making money in the stock market is patience. The fact that you buy a stock does not mean that the price has to go up! Many novice investors would sell at the first sign of a softness in the price. When the price goes up again they blame themselves for not having enough patience. But the next time they buy a stock, they repeat the same mistake again.</p>
</div>

<h2 class="section-head abs" style="left:126px;top:755px">OUR <span>TIPS</span></h2>
<div class="rule abs" style="left:126px;top:777px;width:599px"></div>

<div class="tip-photo abs" style="left:125px;background:linear-gradient(135deg,#0d3f8a,#2f7fd6 60%,#7fb6ee)" role="img" aria-label="Blue stock price screen with figures"></div>
<div class="tip-photo abs" style="left:277px;background:linear-gradient(135deg,#f2a23a,#d9801a 60%,#b8650e)" role="img" aria-label="Orange financial chart with a pen"></div>
<div class="tip-photo abs" style="left:428px;background:linear-gradient(135deg,#f1f1f1,#cfd4d8 60%,#9aa3aa)" role="img" aria-label="Compass with a blue needle"></div>
<div class="tip-photo abs" style="left:581px;background:linear-gradient(135deg,#4a4a4a,#2c2c2c 60%,#1a1a1a)" role="img" aria-label="Businessman drawing a rising red chart line"></div>

<div class="tip-title abs" style="left:124px">STOCK MARKETS</div>
<div class="tip-title abs" style="left:276px">HEDGE FUNDS</div>
<div class="tip-title abs" style="left:427px">DEAL-MAKING</div>
<div class="tip-title abs" style="left:580px">INVESTMENTS</div>
<p class="tip-text abs" style="left:124px">Lorem ipsum dolor sit amet, consecte-tur adipiscing elit, sed do eiusmod tempor incididunt</p>
<p class="tip-text abs" style="left:276px">Lorem ipsum dolor sit amet, consecte-tur adipiscing elit, sed do eiusmod tempor incididunt</p>
<p class="tip-text abs" style="left:427px">Lorem ipsum dolor sit amet, consecte-tur adipiscing elit, sed do eiusmod tempor incididunt</p>
<p class="tip-text abs" style="left:580px">Lorem ipsum dolor sit amet, consecte-tur adipiscing elit, sed do eiusmod tempor incididunt</p>

<h2 class="section-head abs" style="left:128px;top:1009px">OUR <span>PORTFOLIO</span></h2>
<svg class="carousel-arrow abs" style="left:695px" width="8" height="10" viewBox="0 0 8 10"><path d="M6 1 2 5l4 4" fill="none" stroke="#bbb" stroke-width="1.2"/></svg>
<svg class="carousel-arrow abs" style="left:717px" width="8" height="10" viewBox="0 0 8 10"><path d="M2 1l4 4-4 4" fill="none" stroke="#bbb" stroke-width="1.2"/></svg>
<div class="rule abs" style="left:128px;top:1033px;width:597px"></div>

<div class="client abs" style="left:128px;color:#1d5fae"><i style="background:#1d5fae"></i>Velmora</div>
<div class="client abs" style="left:196px;color:#1d5fae"><i style="background:#1d5fae"></i>Quendra Group</div>
<div class="client abs" style="left:334px;color:#333"><i style="background:#333"></i>Harlow Assurance</div>
<div class="client abs" style="left:476px;color:#222"><i style="background:#1e88e5"></i>Lumen Brook</div>
<div class="client abs" style="left:582px;color:#1a3e8c"><i style="background:#1a3e8c"></i>Ostrel</div>
<div class="client abs" style="left:652px;color:#222">Brindle Shoes</div>

<footer class="site-footer abs">
  <nav class="footer-nav">
    <a style="left:321px">Home</a>
    <a style="left:373px">About Us</a>
    <a style="left:437px">Portfolio</a>
    <a style="left:500px">Contact</a>
  </nav>
  <div class="copyright abs">© 2014 Tavel Corporation. All rights reserved.</div>
</footer>

</body>
</html>
```